BLS Business Card 2018

Larkmere Chiropractic. We have two locations that we want to advertise on the same card. Brightvale OrthoCore campus address: 3815 Pellham Dr., Suite 240, Flowood, MS 39417. Madison address: 246 Willowmere Dr., Building D., Madison, MS 39284. website: www.drlarkmere-example.com. o:(601)555-0147 f:(601)555-0183

Target Market(s)

Health care decision makers: primary care doctors and mothers

Contact Information for Business Card

I have no idea; up for any suggestions and I'd do much better picking from examples versus describing what I'm looking for. We are in a very high end location and would like the cards to look really sharp.

Requirements
Must have
• My name, Martin R Belvane, D.C.

```html
<!DOCTYPE html>
<html lang="en">
<head>
<meta charset="utf-8">
<title>Larkmere Chiropractic – Business Card</title>
<link href="https://fonts.googleapis.com/css2?family=Cinzel:wght@400;700&family=PT+Sans:wght@400&display=swap" rel="stylesheet">
<style>
  :root {
    --page-bg: #e9e6e2;
    --card-bg: #050505;
    --ink: #ffffff;
    --figure-light: #f4f4f4;
    --figure-mid: #bdbdbd;
    --figure-dark: #2a2a2a;
  }
  html, body {
    margin: 0;
    width: 1200px;
    height: 900px;
    overflow: hidden;
    background: var(--page-bg);
  }
  .business-card {
    position: absolute;
    left: 111px;
    top: 147px;
    width: 978px;
    height: 606px;
    background: var(--card-bg);
    color: var(--ink);
    overflow: hidden;
    box-shadow: 0 10px 30px rgba(0,0,0,0.25);
  }
  .brand {
    position: absolute;
    left: 62px;
    top: 88px;
    font-family: "Cinzel", serif;
    font-weight: 400;
    color: var(--ink);
    line-height: 1;
    letter-spacing: 0.5px;
  }
  .brand-name { display: block; font-size: 50px; }
  .brand-line { display: block; font-size: 30px; margin-top: 4px; letter-spacing: 1.5px; }
  .doctor-name {
    position: absolute;
    left: 42px;
    top: 236px;
    margin: 0;
    font-family: "Cinzel", serif;
    font-weight: 700;
    font-size: 31px;
    letter-spacing: 0.8px;
  }
  .details {
    position: absolute;
    left: 42px;
    top: 292px;
    font-family: "PT Sans", sans-serif;
    font-size: 24px;
    line-height: 35px;
    z-index: 2;
  }
  .details p { margin: 0; }
  .details .group + .group { margin-top: 11px; }
  .hero-figure {
    position: absolute;
    left: 640px;
    top: 172px;
    width: 338px;
    height: 434px;
    border-radius: 48% 40% 0 30% / 30% 20% 0 40%;
    background: radial-gradient(ellipse at 55% 45%, var(--figure-light) 0%, var(--figure-mid) 55%, var(--figure-dark) 100%);
    z-index: 1;
  }
</style>
</head>
<body>
  <div class="business-card">
    <div class="brand">
      <span class="brand-name">LARKMERE</span>
      <span class="brand-line">CHIROPRACTIC</span>
    </div>

    <h1 class="doctor-name">MARTIN R BELVANE, D.C.</h1>

    <div class="details">
      <div class="group">
        <p>P: (601)555-0147|F: (601)555-0183</p>
        <p>www.drlarkmere-example.com</p>
      </div>
      <div class="group">
        <p>BRIGHTVALE ORTHOCORE CAMPUS</p>
        <p>3815 Pellham Drive, Suite 240</p>
        <p>Flowood, MS 39417.</p>
      </div>
      <div class="group">
        <p>MADISON</p>
        <p>246 Willowmere Dr., Building D., Madison, MS 39284.</p>
      </div>
    </div>

    <div class="hero-figure" role="img" aria-label="White silhouette illustration of an athletic figure reaching upward"></div>
  </div>
</body>
</html>
```